Business Card Design

I need business cards designed for a new company i have started that makes cakes, particularly themed kids cakes with a really modern design and I would like to have my business cards reflect this. I have attached some photos of cakes I have made and would like some to be used.

Industry/Entity Type

Business

Contact Information for Business Card

Business Name: Tarts and Treats by Maren
Mobile: 0492 815 063
email: maren@tartsandtreatsbymaren.example.au
Instagram: instagram.com/tartsandtreatsbymaren/
Facebook: fb.me/tartsandtreatsbymaren

Colors
e667a6
b768aa
3276b5

Requirements
Must have
• Business Name: Tarts and Treats by Maren
• Mobile: 0492 815 063
• email: maren@tartsandtreatsbymaren.example.au
• Instagram: instagram.com/tartsandtreatsbymaren/
• Facebook: fb.me/tartsandtreatsbymaren
Nice to have
• 2 to 3 pictures of my cakes

```html
<!DOCTYPE html>
<html lang="en">
<head>
<meta charset="utf-8">
<title>Tarts and Treats by Maren – Business Card</title>
<link rel="stylesheet" href="https://fonts.googleapis.com/css2?family=Source+Sans+3:wght@400;600&display=swap">
<style>
  :root {
    --backdrop: #e8e4e1;
    --card: #f6f3f4;
    --berry-light: #d8457f;
    --berry-deep: #b3245d;
    --berry-ink: #b8307a;
    --ring: #c9437f;
    --on-berry: #fbeef4;
    --swirl: #ffffff;
  }
  html, body {
    margin: 0;
    width: 1200px;
    height: 969px;
    overflow: hidden;
    background: var(--backdrop);
    font-family: "Source Sans 3", "Myriad Pro", Arial, sans-serif;
  }
  .business-card {
    position: absolute;
    left: 100px;
    top: 200px;
    width: 1000px;
    height: 569px;
    background: var(--card);
    overflow: hidden;
    box-shadow: 0 10px 30px rgba(0,0,0,0.12);
  }
  .wave-art {
    position: absolute;
    inset: 0;
  }
  .brand {
    position: absolute;
    left: 66px;
    top: 75px;
    width: 316px;
    height: 316px;
    border: 3px solid var(--ring);
    border-radius: 50%;
    box-sizing: border-box;
    display: flex;
    align-items: center;
    justify-content: center;
  }
  .brand-name {
    margin: 0;
    text-align: center;
    color: var(--berry-ink);
    font-weight: 600;
    font-size: 62px;
    line-height: 0.95;
  }
  .brand-name span { display: block; }
  .brand-name .amp { font-size: 40px; }
  .contact-block {
    position: absolute;
    right: 48px;
    top: 275px;
    text-align: right;
    color: var(--on-berry);
  }
  .person-name {
    margin: 0;
    font-size: 33px;
    font-weight: 600;
    letter-spacing: 0.5px;
    line-height: 1.1;
    padding-right: 2px;
  }
  .person-role {
    margin: 2px 0 28px;
    font-size: 26px;
    font-weight: 400;
    padding-right: 2px;
  }
  .contact-list {
    list-style: none;
    margin: 0;
    padding: 0;
  }
  .contact-item {
    display: flex;
    justify-content: flex-end;
    align-items: center;
    gap: 16px;
    font-size: 21px;
    height: 38px;
    white-space: nowrap;
  }
  .contact-icon {
    width: 22px;
    height: 22px;
    flex: none;
  }
</style>
</head>
<body>
  <main class="business-card">
    <svg class="wave-art" width="1000" height="569" viewBox="0 0 1000 569" aria-hidden="true">
      <path fill="var(--berry-light)" d="M0 430 C120 500 260 530 400 440 S700 150 1000 80 L1000 569 L0 569 Z"/>
      <path fill="var(--berry-deep)" d="M0 478 C130 548 280 565 430 470 S730 185 1000 130 L1000 569 L0 569 Z" opacity="0.85"/>
      <path fill="none" stroke="var(--swirl)" stroke-width="4" d="M0 458 C125 526 270 552 415 460 S715 168 1000 106"/>
    </svg>

    <div class="brand">
      <h1 class="brand-name"><span>Tarts</span><span class="amp">&amp;</span><span>Treats</span></h1>
    </div>

    <section class="contact-block">
      <p class="person-name">MAREN ADLER</p>
      <p class="person-role">CEO/Founder</p>
      <ul class="contact-list">
        <li class="contact-item">0492 815 063
          <svg class="contact-icon" viewBox="0 0 22 22" aria-label="Mobile"><rect x="6" y="1" width="10" height="20" rx="2" fill="none" stroke="var(--on-berry)" stroke-width="2"/><circle cx="11" cy="17" r="1.3" fill="var(--on-berry)"/></svg>
        </li>
        <li class="contact-item">maren@tartsandtreatsbymaren.example.au
          <svg class="contact-icon" viewBox="0 0 22 22" aria-label="Email"><rect x="1" y="5" width="20" height="13" fill="none" stroke="var(--on-berry)" stroke-width="2"/><path d="M1 5 L11 13 L21 5" fill="none" stroke="var(--on-berry)" stroke-width="2"/></svg>
        </li>
        <li class="contact-item">tartsandtreatsbymaren
          <svg class="contact-icon" viewBox="0 0 22 22" aria-label="Instagram"><rect x="2" y="2" width="18" height="18" fill="var(--on-berry)"/></svg>
        </li>
        <li class="contact-item">tartsandtreatsbymaren
          <svg class="contact-icon" viewBox="0 0 22 22" aria-label="Facebook"><rect x="2" y="2" width="18" height="18" fill="var(--on-berry)"/></svg>
        </li>
      </ul>
    </section>
  </main>
</body>
</html>
```